Willow Cradle Pregnancy and Baby Massage

I need a web design for a new business, WILLOW CRADLE PREGNANCY AND BABY MASSAGE that I am in the process of setting up in the suburbs of Perth, Western Australia. The business is owned and operated by myself and my intention is to service Pregnant Mothers and Parents of Young Babies that would benefit from massage. I would like to have a "Home Page" and pages for "About Me", "Pregnancy Massage", "Baby Massage", a Pricing Page for Pregnancy Massage Sessions, a Pricing Page for Baby Massage Sessions, and a "Contact Me" page to allow clients to either contact me with queries or book available pregnancy massage sessions on a particular day of the week. I would also like a "News" page that would include articles I have written, news about new courses and a link to my Facebook page (yet to be set up). I would like to keep the colour schemes similar to my logo design colours. I need the design to be easy to follow and to appeal to a younger audience (20's to mid 30's).
The target audience is pregnant mothers-to-be wishing to receive massage treatments, and new parents and grandparents of small babies that would like to learn how to massage their babies.
The look and feel should be modern, professional, elegant and feminine.
I need the design to be in a standard format such that I can update the content by myself ( and does not need specialised software) as the company and business progresses.

Target Market(s)

Contact Information for Business Card

Card should have rounded edges. Design should have the same "feel" as the website. Contact Details of my business address, mobile phone, email and website should be included.

Font styles to use
Script

Requirements
Must have
• Same colours as logo design. In cmyk system, the colours are: 20,60,0,0 which best result is pantone 681 and 40,40,0,0 which best result is pantone 2645. Card should include the logo design.

```html
<!DOCTYPE html>
<html lang="en">
<head>
<meta charset="utf-8">
<title>Willow Cradle Pregnancy and Baby Massage</title>
<link rel="stylesheet" href="https://fonts.googleapis.com/css2?family=Questrial&family=Open+Sans:wght@400&display=swap">
<style>
  :root {
    --plum: #b0609f;
    --lavender: #b19cc9;
    --blush: #e4c5de;
    --ink: #444444;
    --nav-bg: rgba(58, 54, 58, 0.92);
    --footer-bg: #544a78;
    --strip-bg: #f6ebf0;
    --white: #ffffff;
    --badge: #d9b6d3;
    --social: #4f4577;
  }
  * { margin: 0; padding: 0; box-sizing: border-box; }
  html, body { width: 930px; height: 1200px; overflow: hidden; background: var(--white); }
  body { position: relative; font-family: "Questrial", sans-serif; color: var(--ink); }

  .hero { position: absolute; left: 0; top: 0; width: 930px; height: 560px; }
  .hero-photo {
    position: absolute; inset: 0;
    background:
      radial-gradient(ellipse 130px 110px at 58% 30%, rgba(238, 196, 170, 0.95) 0%, rgba(238, 196, 170, 0) 100%),
      radial-gradient(ellipse 150px 120px at 72% 40%, rgba(232, 186, 160, 0.85) 0%, rgba(232, 186, 160, 0) 100%),
      radial-gradient(ellipse 200px 150px at 62% 68%, rgba(230, 130, 105, 0.95) 0%, rgba(230, 130, 105, 0) 100%),
      radial-gradient(ellipse 140px 110px at 30% 30%, rgba(222, 120, 95, 0.85) 0%, rgba(222, 120, 95, 0) 100%),
      radial-gradient(ellipse 110px 200px at 90% 40%, rgba(222, 205, 190, 0.75) 0%, rgba(222, 205, 190, 0) 100%),
      radial-gradient(ellipse 160px 90px at 55% 12%, rgba(220, 204, 192, 0.7) 0%, rgba(220, 204, 192, 0) 100%),
      linear-gradient(135deg, #8c6c72 0%, #7a5f66 40%, #6e5860 70%, #5d4c55 100%);
  }
  .hero-wave { position: absolute; left: 0; top: 0; width: 930px; height: 560px; }

  .nav-bar {
    position: absolute; left: 0; top: 0; width: 930px; height: 32px;
    background: var(--nav-bg);
  }
  .nav-menu { position: absolute; left: 367px; top: 10px; display: flex; gap: 21px; list-style: none; }
  .nav-menu li { font-size: 10.5px; color: #e2dde2; white-space: nowrap; }
  .nav-menu li.is-current { color: var(--white); text-decoration: underline; }

  .brand-card {
    position: absolute; left: 102px; top: 0; width: 219px; height: 139px;
    background: var(--white); border-radius: 0 0 16px 16px;
    box-shadow: 0 2px 6px rgba(0,0,0,0.15);
  }
  .brand-card-inner {
    position: absolute; left: 6px; top: -2px; right: 6px; bottom: 8px;
    border: 1.5px dashed #555; border-top: none; border-radius: 0 0 12px 12px;
    display: flex; flex-direction: column; align-items: center; justify-content: center; gap: 10px;
  }
  .brand-dot { width: 32px; height: 32px; border-radius: 50%; background: var(--plum); }
  .brand-name { font-size: 13px; line-height: 17px; color: var(--plum); text-align: center; white-space: nowrap; }

  .hero-arrow { position: absolute; top: 242px; width: 16px; height: 24px; }
  .hero-arrow.prev { left: 30px; }
  .hero-arrow.next { left: 890px; }

  .hero-intro {
    position: absolute; left: 103px; top: 286px; width: 275px;
    font-size: 14.8px; line-height: 21px; color: var(--white);
  }

  .vision-photo-frame {
    position: absolute; left: 104px; top: 579px; width: 302px; height: 302px;
    border: 1.5px dashed #555; border-radius: 50%;
  }
  .vision-photo {
    position: absolute; left: 12px; top: 12px; width: 276px; height: 276px; border-radius: 50%;
    background:
      radial-gradient(ellipse 70px 80px at 36% 38%, rgba(228, 196, 178, 0.95) 0%, rgba(228, 196, 178, 0) 100%),
      radial-gradient(ellipse 70px 80px at 62% 38%, rgba(232, 202, 186, 0.95) 0%, rgba(232, 202, 186, 0) 100%),
      radial-gradient(ellipse 110px 60px at 48% 76%, rgba(170, 110, 110, 0.9) 0%, rgba(170, 110, 110, 0) 100%),
      radial-gradient(circle at 50% 50%, #8a6a5c 0%, #6e5446 55%, #4e3c32 100%);
  }
  .vision-text { position: absolute; left: 464px; top: 590px; width: 360px; }
  .vision-title { font-size: 24px; line-height: 32px; font-weight: 400; color: var(--plum); margin-bottom: 3px; }
  .vision-text p { font-size: 14.4px; line-height: 21px; margin-bottom: 21px; }

  .trust-strip {
    position: absolute; left: 0; top: 952px; width: 930px; height: 161px;
    background:
      radial-gradient(circle 40px at 88% 30%, rgba(240, 170, 195, 0.5) 0%, rgba(240, 170, 195, 0) 100%),
      radial-gradient(circle 50px at 66% 75%, rgba(240, 170, 195, 0.45) 0%, rgba(240, 170, 195, 0) 100%),
      radial-gradient(circle 30px at 4% 85%, rgba(240, 170, 195, 0.45) 0%, rgba(240, 170, 195, 0) 100%),
      radial-gradient(circle at 50% 60%, #fbf4f7 0%, var(--strip-bg) 60%, #f3dde7 100%);
  }
  .cert-badge { position: absolute; left: 110px; top: 22px; width: 194px; height: 116px; border-radius: 10px; background: var(--badge); opacity: 0.6; }
  .follow-label { position: absolute; left: 759px; top: 53px; font-size: 12px; color: #333; }
  .social-dot { position: absolute; left: 776px; top: 74px; width: 36px; height: 36px; border-radius: 50%; background: var(--social); }

  .site-footer {
    position: absolute; left: 0; top: 1113px; width: 930px; height: 87px;
    background: var(--footer-bg); color: #e8e4f1; font-family: "Open Sans", sans-serif; text-align: center;
  }
  .footer-links { margin-top: 26px; font-size: 9px; word-spacing: 1px; }
  .footer-links span { margin: 0 5px; }
  .copyright { margin-top: 11px; font-size: 9px; }
</style>
</head>
<body>
  <header class="hero">
    <div class="hero-photo" role="img" aria-label="Photograph of two sleeping newborn twins wrapped in a coral cloth on a lace heart backdrop"></div>
    <svg class="hero-wave" viewBox="0 0 930 560" aria-hidden="true">
      <path d="M0 520 C120 470 260 440 400 455 C560 470 640 505 760 496 C840 490 890 460 930 432 L930 560 L0 560Z" fill="var(--lavender)"/>
      <path d="M0 524 C140 480 280 470 420 482 C560 495 660 512 780 500 C850 492 900 470 930 455 L930 560 L0 560Z" fill="var(--blush)"/>
      <path d="M0 527 C180 475 300 505 470 506 C650 507 800 480 930 537 L930 560 L0 560Z" fill="var(--white)"/>
    </svg>

    <nav class="nav-bar">
      <ul class="nav-menu">
        <li class="is-current">Home</li>
        <li>About Me</li>
        <li>Pregnancy Massage</li>
        <li>Baby Massage</li>
        <li>Pricing</li>
        <li>News</li>
        <li>Contact Me</li>
      </ul>
    </nav>

    <div class="brand-card">
      <div class="brand-card-inner">
        <span class="brand-dot"></span>
        <span class="brand-name">Willow Cradle<br>Pregnancy and Baby Massage</span>
      </div>
    </div>

    <svg class="hero-arrow prev" viewBox="0 0 16 24" aria-hidden="true"><path d="M12 3 L4 12 L12 21" fill="none" stroke="#fff" stroke-width="3"/></svg>
    <svg class="hero-arrow next" viewBox="0 0 16 24" aria-hidden="true"><path d="M4 3 L12 12 L4 21" fill="none" stroke="#fff" stroke-width="3"/></svg>

    <p class="hero-intro">Willow Cradle Pregnancy and Baby Massage was launched in 2017, offering massage for pregnant women, and instruction of baby massage to parents, grandparents and carers.</p>
  </header>

  <section class="vision">
    <div class="vision-photo-frame">
      <div class="vision-photo" role="img" aria-label="Photograph of newborn twins sleeping together in a soft woollen nest"></div>
    </div>
    <div class="vision-text">
      <h2 class="vision-title">My Vision</h2>
      <p>My vision is to provide a professional massage service to pregnant mothers and babies that also benefits from my skills and experience as a midwife.</p>
      <p>My expectation is that after each session, my clients should leave feeling relaxed, calm, emotionally nurtured, soothed and supported.</p>
      <p>At all times, I will take the utmost care of your privacy, safety and comfort in what is a very personal, intimate time in your life.</p>
    </div>
  </section>

  <section class="trust-strip" role="img" aria-label="Soft pink background scattered with blurred hearts">
    <div class="cert-badge" aria-label="Certification badge"></div>
    <span class="follow-label">Follow us on</span>
    <span class="social-dot" aria-label="Social page link"></span>
  </section>

  <footer class="site-footer">
    <p class="footer-links">Home<span>|</span>About Me<span>|</span>Pregnancy Massage<span>|</span>Baby Massage<span>|</span>Pricing<span>|</span>News<span>|</span>Contact Me</p>
    <p class="copyright">Copyright &copy; 2017 Willow Cradle Pregnancy &amp; Baby Massage. &nbsp;All rights reserved.</p>
  </footer>
</body>
</html>
```